Clean business card with logo provided

I want a card that will stand out among the masses. I need the color and image to show professionalism and yet have a family appeal showing that I only deal with win/win scenarios. The back of the card will be used to take notes about the individual so I can use that in my database entry. I like modern design but need professionalism in it also. It needs to fit my "clean, safe, and affordable housing" motto. I need to be able to write on the file and update the card details for my employees.

Target Market(s)

Investors looking to make investment income through real estate

Industry/Entity Type

Real Estate

Contact Information for Business Card

Brent Kovalich
blank address, city, st, zip code
480-555-3174
brentkovalich@ridgeworthrentals.example
www.ridgeworthrentals.example

Font styles to use
Sans Serif

Requirements
Must have
• I would like the back of the card to have lines for info. example
• Met/Visited: Date:
• Interets:
Nice to have
• I want the cards color to match the logo background color. Font with details to be san serif and black. I want the card rectangular with square corners. Standard business card size. I would like to see cards designed with both images to see which i prefer more.

```html
<!DOCTYPE html>
<html lang="en">
<head>
<meta charset="utf-8">
<title>Ridgeworth Rentals LLC – Business Card</title>
<link href="https://fonts.googleapis.com/css2?family=Cinzel:wght@400;500&family=Open+Sans:wght@400;600&display=swap" rel="stylesheet">
<style>
  :root {
    --backdrop: #8c8c8c;
    --teal: #0aa1b6;
    --paper: #e7e8ea;
    --ink: #111416;
    --card-black: #000000;
    --rule: #2a2d30;
  }
  * { margin: 0; padding: 0; box-sizing: border-box; }
  html, body {
    width: 1105px; height: 1200px; overflow: hidden;
    background: var(--backdrop);
    font-family: "Open Sans", Arial, sans-serif;
  }
  .canvas { position: relative; width: 1105px; height: 1200px; }

  .card {
    position: absolute; left: 182px; width: 747px; height: 427px;
    box-shadow: 0 14px 22px rgba(0,0,0,0.35);
  }

  /* Front */
  .card-front { top: 119px; display: flex; }
  .contact-panel {
    position: relative; width: 366px; height: 100%;
    background: var(--teal); color: var(--ink);
  }
  .notes-panel { position: relative; flex: 1; background: var(--paper); }
  .divider {
    position: absolute; left: 366px; top: 30px; bottom: 0;
    width: 3px; background: var(--rule);
  }
  .holder-name {
    position: absolute; left: 38px; top: 133px;
    font-family: "Cinzel", Georgia, serif; font-weight: 500;
    font-size: 30px; letter-spacing: 0.5px; color: var(--ink);
  }
  .address {
    position: absolute; left: 38px; top: 180px;
    font-size: 19px; line-height: 25px; color: var(--ink);
  }
  .contact-list {
    position: absolute; left: 38px; top: 243px; list-style: none;
    font-size: 18px; line-height: 29px; color: var(--ink);
  }
  .contact-list li { display: flex; align-items: center; gap: 9px; white-space: nowrap; }
  .contact-list .email { font-size: 14.5px; letter-spacing: -0.1px; }
  .contact-list svg { width: 18px; height: 18px; flex: none; }

  .note-row {
    position: absolute; left: 21px; right: 15px;
    display: flex; align-items: flex-end; gap: 4px;
    color: var(--teal); font-size: 19px; text-transform: uppercase;
  }
  .note-row .write-line { flex: 1; border-bottom: 2px solid var(--ink); margin-bottom: 4px; }
  .note-line {
    position: absolute; left: 25px; right: 15px;
    border-bottom: 2px solid var(--ink);
  }
  .row-met { top: 54px; }
  .line-met { top: 139px; }
  .row-date { top: 176px; }
  .row-interests { top: 240px; right: 19px; }
  .line-interests { top: 294px; }

  /* Back */
  .card-back {
    top: 637px; background: var(--card-black);
    display: flex; flex-direction: column; align-items: center; justify-content: center;
  }
  .brand-name {
    font-family: "Cinzel", Georgia, serif; font-weight: 500;
    font-size: 44px; letter-spacing: 3px; color: var(--teal);
    margin-top: -6px;
  }
  .tagline {
    margin-top: 14px; font-size: 13px; letter-spacing: 0.6px; color: var(--teal);
  }
</style>
</head>
<body>
<main class="canvas">

  <section class="card card-front" aria-label="Business card front">
    <div class="contact-panel">
      <h1 class="holder-name">BRENT KOVALICH</h1>
      <p class="address">1420 Juniper Court<br>Fairbanks, Alaska 99701</p>
      <ul class="contact-list">
        <li>
          <svg viewBox="0 0 24 24" aria-hidden="true"><path fill="#111416" d="M6.6 10.8a15.1 15.1 0 0 0 6.6 6.6l2.2-2.2c.3-.3.7-.4 1-.2 1.1.4 2.3.6 3.6.6.6 0 1 .4 1 1V20c0 .6-.4 1-1 1A17 17 0 0 1 3 4c0-.6.4-1 1-1h3.5c.6 0 1 .4 1 1 0 1.3.2 2.5.6 3.6.1.3 0 .7-.2 1z"/></svg>
          480-555-3174
        </li>
        <li class="email">
          <svg viewBox="0 0 24 24" aria-hidden="true"><path fill="#111416" d="M2 5h20v14H2z"/><path fill="none" stroke="#0aa1b6" stroke-width="1.8" d="M2.5 5.5 12 13l9.5-7.5"/></svg>
          brentkovalich@ridgeworthrentals.example
        </li>
        <li>
          <svg viewBox="0 0 24 24" aria-hidden="true"><circle cx="12" cy="12" r="10" fill="#111416"/><path fill="none" stroke="#0aa1b6" stroke-width="1.4" d="M2 12h20M12 2c3 3 3 17 0 20M12 2c-3 3-3 17 0 20"/></svg>
          www.ridgeworthrentals.example
        </li>
      </ul>
    </div>
    <div class="notes-panel">
      <div class="note-row row-met"><span>Met/Visited:</span><span class="write-line"></span></div>
      <div class="note-line line-met"></div>
      <div class="note-row row-date"><span>Date:</span><span class="write-line"></span></div>
      <div class="note-row row-interests"><span>Interests:</span><span class="write-line"></span></div>
      <div class="note-line line-interests"></div>
    </div>
    <div class="divider"></div>
  </section>

  <section class="card card-back" aria-label="Business card back">
    <p class="brand-name">RIDGEWORTH RENTALS LLC</p>
    <p class="tagline">Providing clean, safe, and affordable housing</p>
  </section>

</main>
</body>
</html>
```